Update patient consent forms and contract

Objective
Redesign the existing patient contract information document to create a modern,contempory, and easy-to-understand experience for patients. The updated design should improve readability, accessibility, and overall presentation while maintaining compliance with healthcare and legal requirements.

Key Deliverables

Refreshed visual design and layout
Improved information hierarchy and readability
Modern typography and colour palette aligned with brand guidelines
Clear section headings and navigation
Print-ready and digital versions (PDF)

Include KEV Logo within patient KEV consent to treatment. Ideally this document should be portrait not landscape.
Updates

I would love a front page to be included in the document

```html
<!DOCTYPE html>
<html lang="en">
<head>
<meta charset="utf-8">
<title>Lumen Orthodontics – Patient Documents</title>
<link href="https://fonts.googleapis.com/css2?family=Outfit:wght@300;400;500;600;700&display=swap" rel="stylesheet">
<style>
:root{
  --navy:#163a5f;
  --cyan:#1d9ad8;
  --white:#ffffff;
  --ink:#1d2b3a;
  --mute:#a9b8c7;
  --stage:#b5b6b8;
  --foot:#f4f6f8;
}
*{margin:0;padding:0;box-sizing:border-box}
html,body{width:1200px;height:582px;overflow:hidden}
body{background:var(--stage);font-family:'Outfit',sans-serif;position:relative;color:var(--white)}
.page{position:absolute;top:86px;width:317px;height:410px;background:var(--navy);box-shadow:2px 3px 6px rgba(0,0,0,.25);overflow:hidden}
.page-retainer{left:101px}
.page-payment{left:442px}
.page-consent{left:782px}

/* brand name lockups: plain name plus one plain shape */
.brand{position:absolute;display:flex;align-items:center;gap:4px;color:var(--mute);font-weight:500;white-space:nowrap}
.brand .dot{border-radius:50%;background:var(--mute)}
.brand .square{background:var(--mute)}

/* retainer page */
.retainer-title{position:absolute;top:75px;left:34px;right:20px;display:flex;align-items:center;gap:6px;color:var(--cyan);font-size:13px;font-weight:600}
.retainer-title::before,.retainer-title::after{content:"";flex:1;height:.6px;background:var(--cyan)}
.retainer-body{position:absolute;top:98px;left:20px;width:277px;font-size:6.15px;line-height:11.3px;text-align:justify;font-weight:300}
.retainer-body .accent{color:var(--cyan);font-weight:500}

/* footer */
.footer{position:absolute;left:0;right:0;bottom:0;height:56px;display:flex;background:var(--foot);color:var(--ink)}
.footer .bank{width:102px;background:var(--cyan);color:var(--white);padding:8px 0 0 18px}
.footer h4{font-size:4.6px;font-weight:600;margin-bottom:4px}
.bank-row{display:flex;font-size:3.6px;line-height:9px}
.bank-row span:first-child{width:42px;opacity:.85}
.bank-row span:last-child{font-weight:600}
.footer .info{width:107px;padding:8px 0 0 10px}
.footer .spec{flex:1;padding:2px 0 0 10px;border-left:.5px solid #c7d0d9;margin:6px 0}
.contact{display:flex;align-items:center;gap:4px;font-size:3.7px;line-height:8.5px}
.contact svg{width:5px;height:5px;flex:none}
.doctor{display:flex;gap:3px;font-size:3.6px;line-height:4px;margin-bottom:3.5px}
.doctor b{font-weight:600;display:block}
.doctor svg{width:5px;height:6px;flex:none;margin-top:1px}

/* payment page */
.pay-title{position:absolute;top:14px;left:18px;font-size:11px;font-weight:700}
.pay-lead{position:absolute;top:35px;left:18px;font-size:5.5px;font-weight:600}
.pay-intro{position:absolute;top:47px;left:18px;width:283px;font-size:5.3px;line-height:9.5px;font-weight:300}
.pay-sub{position:absolute;left:18px;color:var(--cyan);font-size:8.5px;font-weight:600}
.option{position:absolute;left:18px;display:flex;align-items:center;gap:5px;font-size:5.7px;font-weight:600}
.option .check{width:11px;height:11px;background:var(--white);border-radius:1.5px}
.pay-text{position:absolute;left:18px;width:280px;font-size:5.3px;line-height:7.3px;font-weight:300}
.pay-text b{font-weight:600}
.pay-icon{position:absolute;width:30px;height:26px;opacity:.45}
.divider{position:absolute;left:18px;width:276px;top:159px;border-top:.6px dashed #6f8aa6}
.declaration{position:absolute;left:0;right:0;top:274px;height:80px;background:var(--white);color:var(--ink);text-align:center}
.declaration h3{margin-top:4px;color:var(--cyan);font-size:9px;font-weight:600}
.declaration p{font-size:5.4px;margin-top:3px}
.sign{position:absolute;top:60px;width:54px;border-top:.6px solid var(--ink);font-size:6.3px;font-weight:600;padding-top:1px}

/* consent page */
.sec{position:absolute;font-size:2.9px;line-height:4.6px;font-weight:300;text-align:justify}
.sec-left{left:10px;width:150px}
.sec-right{left:163px;width:143px}
.sec h5{font-size:5.4px;font-weight:600;line-height:6px;margin-bottom:1px}
.sec h6{color:var(--cyan);font-size:3.9px;font-weight:600;line-height:5px;margin-bottom:.5px}
.consent-card{position:absolute;left:164px;top:279px;width:141px;height:131px;background:var(--white);color:var(--ink);padding:8px 8px 0}
.consent-card .brand{color:#8d9caa}
.consent-card .brand .dot,.consent-card .brand .square{background:#8d9caa}
.consent-card h3{color:var(--cyan);font-size:6.2px;font-weight:600;margin:28px 0 4px;display:flex;gap:4px;align-items:center}
.consent-card h3::before{content:"";width:24px;height:.4px;background:transparent}
.consent-card h3::after{content:"";flex:1;height:.4px;background:#c7d0d9}
.consent-item{font-size:4.2px;line-height:5.6px;padding:2px 0 2px 4px;border-bottom:.5px dotted #9fb0c0;position:relative}
.consent-item::before{content:"";position:absolute;left:0;top:4.5px;width:1.6px;height:1.6px;border-radius:50%;background:var(--cyan)}
</style>
</head>
<body>

<!-- Retainer policy -->
<section class="page page-retainer">
  <div class="brand" style="left:68px;top:32px;font-size:10px"><span class="dot" style="width:9px;height:9px"></span>KEV</div>
  <div class="brand" style="left:170px;top:32px;font-size:10px"><span class="square" style="width:8px;height:8px"></span>Lumen Orthodontics</div>

  <h2 class="retainer-title">Our retainer policy</h2>
  <p class="retainer-body">Wearing your retainers is the most important part of your orthodontic journey. Teeth shifting is a part of the natural ageing process just like getting wrinkles, so lifetime maintenance is crucial. Healthy teeth are not meant to be glued together, they are individual units and function independently. This is normally only done for areas of weak bone and gum or damaged teeth. For this reason <span class="accent">WE DO NOT ENCOURAGE THE USE OF ‘BONDED’ OR ‘PERMANENT’ RETAINERS.</span> Instead we advocate responsible use of removable retainers to maintain your smile. Permanent or bonded retainers are not actually permanent and can cause other unexpected problems after treatment is completed, such as difficulty to clean around those teeth which can cause plaque trapping and lead to localised gum and bone loss. They are subject to breaking frequently, which is the reason that when bonded retainers are placed, it is recommended that you still wear a removable retainer over them anyway. Bonded retainers only hold the front few teeth, whereas your orthodontic treatment involved improvements of ALL your teeth. Thus, holding the front teeth only gives the back teeth a chance to move out of alignment. The retainers we provide at Lumen Orthodontics, are only worn at night and will hold ALL your teeth where they are at the end of your orthodontic treatment. Even excellent retainer wear will not guarantee that the teeth will stay exactly the same forever, due to the natural ageing and bone changing processes. Minor alignment adjustments may be made to your retainers in the future to ensure that you remain happy with your smile. After 2 years of retainer reviews, further follow up care may be charged at the current office visit rate. Lost or broken retainers will incur a fee for replacement or repair.</p>

  <footer class="footer">
    <div class="bank">
      <h4>Our bank account details:</h4>
      <div class="bank-row"><span>Account Name</span><span>: Lumen Orthodontics</span></div>
      <div class="bank-row"><span>Bank</span><span>: Harbour Bank</span></div>
      <div class="bank-row"><span>BSB</span><span>: 012 345</span></div>
      <div class="bank-row"><span>Account Number</span><span>: 55501234</span></div>
    </div>
    <div class="info">
      <h4>Information:</h4>
      <div class="contact"><svg viewBox="0 0 10 10"><path d="M5 1a3 3 0 0 1 3 3c0 2-3 5-3 5S2 6 2 4a3 3 0 0 1 3-3z" fill="none" stroke="#1d9ad8"/></svg>48 Harbour Rd, Eastvale VIC 3100</div>
      <div class="contact"><svg viewBox="0 0 10 10"><path d="M2 1h2l1 2-1 1a5 5 0 0 0 2 2l1-1 2 1v2c-4 0-7-3-7-7z" fill="none" stroke="#1d9ad8"/></svg>03 9000 1428</div>
      <div class="contact"><svg viewBox="0 0 10 10"><rect x="1.5" y="2" width="7" height="6" fill="none" stroke="#1d9ad8"/></svg>03 9000 1429</div>
      <div class="contact"><svg viewBox="0 0 10 10"><path d="M1 2h8v6H1zM1 2l4 3 4-3" fill="none" stroke="#1d9ad8"/></svg>hello@lumen-ortho.example</div>
    </div>
    <div class="spec">
      <h4>Registered Specialist Orthodontists:</h4>
      <div class="doctor"><svg viewBox="0 0 10 12"><path d="M2 1c2 0 2 1 3 1s1-1 3-1 2 3 1 5-1 5-2 5-1-3-2-3-1 3-2 3-1-3-2-5 0-5 1-5z" fill="none" stroke="#1d9ad8"/></svg><div><b>Dr Nora Vale</b>MDSc, Grad Dip Clin Dent, BDSc(Hons)</div></div>
      <div class="doctor"><svg viewBox="0 0 10 12"><path d="M2 1c2 0 2 1 3 1s1-1 3-1 2 3 1 5-1 5-2 5-1-3-2-3-1 3-2 3-1-3-2-5 0-5 1-5z" fill="none" stroke="#1d9ad8"/></svg><div><b>Dr Sam Idris</b>MDSc, Grad Dip Clin Dent, MOrth, BDSc</div></div>
      <div class="doctor"><svg viewBox="0 0 10 12"><path d="M2 1c2 0 2 1 3 1s1-1 3-1 2 3 1 5-1 5-2 5-1-3-2-3-1 3-2 3-1-3-2-5 0-5 1-5z" fill="none" stroke="#1d9ad8"/></svg><div><b>Dr Leo Marsh</b>DCD, MOrth, MRACDS (Orth), BDSc (Hons)</div></div>
    </div>
  </footer>
</section>

<!-- Payment option selection -->
<section class="page page-payment">
  <h1 class="pay-title">Payment Option Selection</h1>
  <div class="brand" style="left:163px;top:16px;font-size:7.5px"><span class="dot" style="width:7px;height:7px"></span>KEV</div>
  <div class="brand" style="left:222px;top:16px;font-size:7.5px"><span class="square" style="width:6px;height:6px"></span>Lumen Orthodontics</div>

  <p class="pay-lead">Thank you for choosing Lumen Orthodontics.</p>
  <p class="pay-intro">To assist with managing your treatment fees, please select your preferred payment method below. If you would prefer to pay at each scheduled appointment, please advise our reception team. Please note that appointments are generally scheduled every 6–8 weeks.</p>

  <h3 class="pay-sub" style="top:84px">Please select one option:</h3>
  <div class="option" style="top:99px"><span class="check"></span>Credit Card Direct Debit</div>
  <svg class="pay-icon" style="left:140px;top:98px" viewBox="0 0 30 26"><rect x="1" y="2" width="26" height="17" rx="2" fill="none" stroke="#fff"/><path d="M1 7h26M5 13h8" stroke="#fff"/><circle cx="25" cy="19" r="5" fill="none" stroke="#fff"/><path d="M23 19h4l-1.5-1.5" fill="none" stroke="#fff"/></svg>
  <p class="pay-text" style="top:116px">I would like to pay via credit card direct debit.</p>
  <p class="pay-text" style="top:131px">I understand that Lumen Orthodontics will send me a secure PayLink payment link to enter my credit card details. The card provided will be securely stored and used as my nominated payment method for future scheduled payments relating to my treatment plan.</p>

  <div class="divider"></div>

  <div class="option" style="top:166px"><span class="check"></span>Monthly Direct Bank Transfer</div>
  <svg class="pay-icon" style="left:152px;top:168px;width:26px" viewBox="0 0 26 26"><rect x="1" y="4" width="24" height="20" rx="2" fill="none" stroke="#fff"/><path d="M6 1v6M20 1v6M8 13h10l-2-2M18 17H8l2 2" fill="none" stroke="#fff"/></svg>
  <p class="pay-text" style="top:183px">I would like to pay via monthly direct bank transfer.</p>
  <p class="pay-text" style="top:198px">I understand that I am responsible for ensuring monthly payments are made on time in accordance with my agreed payment arrangement.</p>

  <h3 class="pay-sub" style="top:227px">Important</h3>
  <p class="pay-text" style="top:243px">When making direct transfer payments, please use the <b>patient’s full name</b> as the payment reference (for example: Jane Citizen), rather than the account holder’s name. This ensures payments are correctly allocated to your treatment account.</p>

  <div class="declaration">
    <h3>Patient Declaration</h3>
    <p>I have read and understood the payment options above and agree to my selected payment method.</p>
    <div class="sign" style="left:49px">Signature</div>
    <div class="sign" style="left:214px">Date</div>
  </div>

  <footer class="footer">
    <div class="bank">
      <h4>Our bank account details:</h4>
      <div class="bank-row"><span>Account Name</span><span>: Lumen Orthodontics</span></div>
      <div class="bank-row"><span>Bank</span><span>: Harbour Bank</span></div>
      <div class="bank-row"><span>BSB</span><span>: 012 345</span></div>
      <div class="bank-row"><span>Account Number</span><span>: 55501234</span></div>
    </div>
    <div class="info">
      <h4>Information:</h4>
      <div class="contact"><svg viewBox="0 0 10 10"><path d="M5 1a3 3 0 0 1 3 3c0 2-3 5-3 5S2 6 2 4a3 3 0 0 1 3-3z" fill="none" stroke="#1d9ad8"/></svg>48 Harbour Rd, Eastvale VIC 3100</div>
      <div class="contact"><svg viewBox="0 0 10 10"><path d="M2 1h2l1 2-1 1a5 5 0 0 0 2 2l1-1 2 1v2c-4 0-7-3-7-7z" fill="none" stroke="#1d9ad8"/></svg>03 9000 1428</div>
      <div class="contact"><svg viewBox="0 0 10 10"><rect x="1.5" y="2" width="7" height="6" fill="none" stroke="#1d9ad8"/></svg>03 9000 1429</div>
      <div class="contact"><svg viewBox="0 0 10 10"><path d="M1 2h8v6H1zM1 2l4 3 4-3" fill="none" stroke="#1d9ad8"/></svg>hello@lumen-ortho.example</div>
    </div>
    <div class="spec">
      <h4>Registered Specialist Orthodontists:</h4>
      <div class="doctor"><svg viewBox="0 0 10 12"><path d="M2 1c2 0 2 1 3 1s1-1 3-1 2 3 1 5-1 5-2 5-1-3-2-3-1 3-2 3-1-3-2-5 0-5 1-5z" fill="none" stroke="#1d9ad8"/></svg><div><b>Dr Nora Vale</b>MDSc, Grad Dip Clin Dent, BDSc(Hons)</div></div>
      <div class="doctor"><svg viewBox="0 0 10 12"><path d="M2 1c2 0 2 1 3 1s1-1 3-1 2 3 1 5-1 5-2 5-1-3-2-3-1 3-2 3-1-3-2-5 0-5 1-5z" fill="none" stroke="#1d9ad8"/></svg><div><b>Dr Sam Idris</b>MDSc, Grad Dip Clin Dent, MOrth, BDSc</div></div>
      <div class="doctor"><svg viewBox="0 0 10 12"><path d="M2 1c2 0 2 1 3 1s1-1 3-1 2 3 1 5-1 5-2 5-1-3-2-3-1 3-2 3-1-3-2-5 0-5 1-5z" fill="none" stroke="#1d9ad8"/></svg><div><b>Dr Leo Marsh</b>DCD, MOrth, MRACDS (Orth), BDSc (Hons)</div></div>
    </div>
  </footer>
</section>

<!-- Consent to treatment -->
<section class="page page-consent">
  <div class="sec sec-left" style="top:12px">
    <h5>• ORTHODONTIC TREATMENT</h5>
    <p>Orthodontic treatment aims to create a healthy smile, healthier teeth and gums and a better bite for everyday chewing. Its success depends a great deal on the understanding and co-operation of the patient and family. This form sets out the usual risks and limits of treatment so that you can make an informed choice. Your orthodontist will gladly explain anything you do not understand. While treatment brings many benefits, it also has limits, and other options may exist. You should be clear about what is expected of you, as a patient or as the parent of a young patient, to reach a good result. Please keep in mind that, like other healing arts, results cannot be guaranteed. The main factor in any correction is how each patient responds to treatment. Treatment plans are reviewed at each visit and may be adjusted as your teeth respond. If you have any questions at all, please ask before you sign.</p>
  </div>
  <div class="sec sec-left" style="top:75px">
    <h5>• BENEFITS</h5>
    <p>Orthodontics plays an important role in improving overall oral health and in creating balance and harmony between the face and teeth for a pleasant, healthy smile, which may lift a person’s self esteem. A correct bite helps the muscles and jaw joints work as they should and allows comfortable chewing. Properly aligned teeth are easier to brush and floss, so the risk of decay may be lowered, as may the risk of gum disease and the loss of supporting bone. Aligned teeth are also less likely to suffer heavy wear or injury. Because each patient is different, and because of the limits each case brings, some benefits may not be reached by every patient.</p>
  </div>
  <div class="sec sec-left" style="top:128px">
    <h5>• RISKS</h5>
    <p>All forms of medical and dental treatment, including orthodontics, carry some risk and limits. Happily, problems in orthodontics are uncommon and, when they do occur, they are usually of minor consequence. They should still be weighed when deciding to begin treatment. The main risks are set out below. Please read each one with care.</p>
  </div>
  <div class="sec sec-left" style="top:165px">
    <h6>1. Oral Hygiene</h6>
    <p>Braces do not cause decay, gum disease or white marks on the teeth, but these can occur if sugary food and drink are taken often or if teeth are not brushed well. The same problems can arise without braces, yet the risk is higher while they are worn. Careful brushing, flossing and regular check-ups with your general dentist are vital throughout treatment.</p>
  </div>
  <div class="sec sec-left" style="top:204px">
    <h6>2. Relapse</h6>
    <p>Teeth may tend to shift after treatment ends. Faithful wear of retainers as advised will reduce this. Changes may happen at any time, whether or not a person has had orthodontic treatment, and are common in the late teens while growth of the facial bones is coming to an end. Throughout life the bite can change, and the front teeth are the most likely to move. Causes include the arrival of wisdom teeth, growth changes, mouth breathing, tongue habits and the playing of some wind instruments. In some cases movement may be enough to need a short further course of treatment to restore a good result.</p>
  </div>
  <div class="sec sec-left" style="top:258px">
    <h6>3. Periodontal Health</h6>
    <p>The health of the gums and bone that support the teeth may be affected by orthodontic movement if a problem already exists, and in rare cases where none was seen before. In general, treatment lowers the chance of tooth loss or gum infection caused by a poor bite. Loss of support can occur if plaque is not removed each day with careful brushing and cleaning.</p>
  </div>
  <div class="sec sec-left" style="top:296px">
    <h6>4. Root Shortening</h6>
    <p>In some patients the roots of the teeth may shorten during treatment. It is not possible to say who is prone to this. Mild shortening is usually of no lasting concern, but in rare cases it may affect how long the teeth last. Your orthodontist may take X-rays to check the roots where needed.</p>
  </div>
  <div class="sec sec-left" style="top:330px">
    <h6>5. Jaw Joints</h6>
    <p>Pain or clicking in the jaw joints may occur at any time, with or without orthodontic treatment. Symptoms may include headaches, ear pain or limited opening, and should be reported to your orthodontist. Some people are prone to jaw problems and some are not. Studies show these problems are usually unrelated to treatment. Other care may be needed where pain continues, and discomfort may last from a few days to some weeks.</p>
  </div>
  <div class="sec sec-left" style="top:373px">
    <h6>6. Tooth Vitality</h6>
    <p>A tooth that was injured in the past or has large fillings may lose vitality. Orthodontic movement can, in some cases, bring this problem to light. In rare cases root canal treatment and other dental care may be needed to restore the tooth and its colour.</p>
  </div>

  <div class="sec sec-right" style="top:13px">
    <h6>7. Loose appliances and discomfort</h6>
    <p>The gums, cheeks or lips may be scratched or irritated by new or loose appliances, or by knocks to the mouth. You will be shown how to care for your appliances. Loose parts may very rarely be swallowed or breathed in, so please tell your orthodontist of any unusual symptoms, or of broken or loose parts, as soon as they are noted. Some tenderness is normal after each adjustment, and the length of tenderness differs from patient to patient. It usually lasts one to two days.</p>
  </div>
  <div class="sec sec-right" style="top:62px">
    <h6>8. Atypical Growth</h6>
    <p>Too little, too much or uneven growth of the jaws may limit the result. If growth is out of balance, treatment may take longer. Growth after treatment ends may change the bite and may call for further care. In a few cases of unusual growth, jaw surgery may be needed to reach the best result.</p>
  </div>
  <div class="sec sec-right" style="top:106px">
    <h6>9. Headgear</h6>
    <p>Headgear handled carelessly may cause injury to the face. Do not wear it during rough play or contact sport.</p>
  </div>
  <div class="sec sec-right" style="top:129px">
    <h6>10. Treatment Time</h6>
    <p>The time needed may exceed the estimate. Poor elastic wear, poor oral care, broken appliances and missed visits can all lengthen treatment and affect the result.</p>
  </div>
  <div class="sec sec-right" style="top:159px">
    <h6>11. Co-operation</h6>
    <p>Your co-operation is the best guide to a pleasing smile and bite. Without it, the orthodontist may need to change the goals of treatment, and in rare cases treatment may be stopped early.</p>
  </div>
  <div class="sec sec-right" style="top:191px">
    <h6>12. Ceramic Brackets</h6>
    <p>Where tooth coloured brackets are used, there have been rare reports of enamel chips or cracks when brackets are removed. Broken pieces should be reported, as they could be swallowed.</p>
  </div>
  <div class="sec sec-right" style="top:227px">
    <h6>13. Complementary aesthetic dentistry</h6>
    <p>Where teeth are unusual in number, size or shape, extra care such as bonding, crowns, bridges or gum work may be needed after treatment to complete the smile.</p>
  </div>
  <div class="sec sec-right" style="top:259px">
    <h6>14. General Health</h6>
    <p>General health problems can affect treatment. Please keep your orthodontist informed of any changes to your health.</p>
  </div>

  <div class="consent-card">
    <div class="brand" style="left:14px;top:11px;font-size:6px"><span class="dot" style="width:6px;height:6px"></span>KEV</div>
    <div class="brand" style="left:58px;top:11px;font-size:6px"><span class="square" style="width:5px;height:5px"></span>Lumen Orthodontics</div>
    <h3>CONSENT TO TREATMENT</h3>
    <div class="consent-item">I here by authorize:</div>
    <div class="consent-item">To carry out orthodontic treatment and any other related procedures deemed necessary including X-rays, for the welfare and treatment of:</div>
    <div class="consent-item">Signature of patient or parent/guardian:</div>
    <div class="consent-item">Name :</div>
    <div class="consent-item">Relationship to patient :</div>
    <div class="consent-item">Date :</div>
    <div class="consent-item">Signature of Orthodontis :</div>
  </div>
</section>

</body>
</html>
```